Corvane Paintless Dent Removal

Our company works on vehicles removing dents using a highly skilled trade which the metal is massaged out with special tools without disturbing the original paint, hence paintless dent removal. Besides keeping the paint and metal original its also very environmentally friendly since no paint or toxic fillers are used. Also we we are one of the most experienced companies in the business with 25 years

Target Market(s)

Retail Automobile consumers, Auto Dealerships and Auto Body Shops

Industry/Entity Type

Auto Repair

Contact Information for Business Card

Dale Hollister
PO Box 518 Brookmere, NY 11962
631-555-0148
corvanepdr@mailbox-example.com
website corvanepdr.example
youtube corvane paintless dent removal
25 years of experience removing Dents, Dings and Hail Damage

Font styles to use
Serif
Sans Serif

Colors

Designer to choose colors to be used in the design.

Requirements
Must have
• I do like things that are simple but classy and somewhat bold, also I like my logo so that should be somewhat important

```html
<!DOCTYPE html>
<html lang="en">
<head>
<meta charset="utf-8">
<title>Corvane Paintless Dent Removal – Business Card</title>
<link href="https://fonts.googleapis.com/css2?family=Roboto+Condensed:wght@400;700&display=swap" rel="stylesheet">
<style>
  :root {
    --navy: #13305a;
    --navy-deep: #0f2a50;
    --green: #7dc21e;
    --white: #ffffff;
    --gold: #c9a13b;
    --ink: #1a1a1a;
    --page: #ecebe7;
  }
  * { margin: 0; padding: 0; box-sizing: border-box; }
  html, body { width: 1200px; height: 886px; overflow: hidden; }
  body {
    background: var(--page);
    font-family: "Roboto Condensed", Arial, sans-serif;
    position: relative;
  }
  .card {
    position: absolute;
    top: 288px;
    width: 540px;
    height: 309px;
    overflow: hidden;
    box-shadow: 0 6px 18px rgba(0,0,0,.18);
  }
  .card-front { left: 40px; background: var(--white); }
  .card-back { left: 620px; background: var(--navy-deep); }

  .front-band { position: absolute; inset: 0; }

  .brand-name {
    position: absolute;
    color: var(--navy);
    font-weight: 700;
    text-align: center;
    line-height: 1;
  }
  .front-brand { left: 30px; top: 58px; width: 230px; }
  .brand-name .word { display: block; font-size: 46px; letter-spacing: 1px; }
  .brand-name .tagline { display: block; font-size: 17px; margin-top: 6px; letter-spacing: .3px; }

  .years-seal {
    position: absolute;
    left: 408px; top: 14px;
    width: 52px; height: 52px;
    border-radius: 50%;
    background: var(--gold);
    border: 4px solid var(--ink);
  }

  .contact {
    position: absolute;
    color: var(--white);
    font-size: 13px;
    line-height: 1.45;
  }
  .contact-person { left: 24px; top: 206px; }
  .person-name { font-size: 21px; font-weight: 700; letter-spacing: .5px; text-transform: uppercase; margin-bottom: 6px; }
  .contact-line { display: flex; align-items: center; gap: 8px; }
  .contact-line svg { width: 11px; height: 11px; flex: none; }
  .contact-divider {
    position: absolute;
    left: 292px; top: 214px;
    width: 1px; height: 74px;
    background: rgba(255,255,255,.7);
  }
  .contact-place { left: 308px; top: 224px; font-size: 14px; }

  .back-brand {
    left: 0; right: 0; top: 110px;
    margin: 0 auto;
    width: 320px;
    color: var(--white);
  }
  .back-brand .word { font-size: 58px; }
  .back-brand .tagline { font-size: 20px; }
  .back-web {
    position: absolute;
    left: 22px; top: 50%;
    transform: translate(-50%, -50%) rotate(-90deg) translateY(60px);
    transform-origin: center;
    color: var(--white);
    font-size: 12px;
    letter-spacing: 5px;
    white-space: nowrap;
  }
  .back-rule {
    position: absolute;
    left: 0; right: 0; bottom: 0;
    height: 6px;
    background: var(--green);
  }
</style>
</head>
<body>

<section class="card card-front" aria-label="Business card front">
  <svg class="front-band" viewBox="0 0 540 309" preserveAspectRatio="none" aria-hidden="true">
    <path d="M0 190 H300 C410 190 470 110 540 20 V309 H0 Z" fill="var(--green)"/>
  </svg>

  <div class="brand-name front-brand">
    <span class="word">CORVANE</span>
    <span class="tagline">Paintless Dent Removal</span>
  </div>

  <div class="years-seal" aria-hidden="true"></div>

  <div class="contact contact-person">
    <p class="person-name">Dale Hollister</p>
    <p class="contact-line">
      <svg viewBox="0 0 12 12" aria-hidden="true"><path d="M2.5 1 L4.5 1 L5.3 3.6 L4 4.6 C4.6 6 6 7.4 7.4 8 L8.4 6.7 L11 7.5 L11 9.5 C11 10.3 10.3 11 9.5 11 C5 11 1 7 1 2.5 C1 1.7 1.7 1 2.5 1 Z" fill="var(--white)"/></svg>
      631-555-0148
    </p>
    <p class="contact-line">
      <svg viewBox="0 0 12 12" aria-hidden="true"><rect x="1" y="2.5" width="10" height="7" fill="var(--white)"/><path d="M1 2.5 L6 6.5 L11 2.5" stroke="var(--green)" fill="none"/></svg>
      corvanepdr@mailbox-example.com
    </p>
    <p class="contact-line">
      <svg viewBox="0 0 12 12" aria-hidden="true"><circle cx="6" cy="6" r="5" fill="var(--white)"/></svg>
      corvane paintless dent removal
    </p>
  </div>

  <div class="contact-divider" aria-hidden="true"></div>

  <div class="contact contact-place">
    <p>PO Box 518</p>
    <p>Brookmere, NY 11962</p>
    <p>www.corvanepdr.example</p>
  </div>
</section>

<section class="card card-back" aria-label="Business card back">
  <p class="back-web">www.corvanepdr.example</p>
  <div class="brand-name back-brand">
    <span class="word">CORVANE</span>
    <span class="tagline">Paintless Dent Removal</span>
  </div>
</section>

</body>
</html>
```